New iOS App design for Boston Startup

We are looking for a new app design for our iPhone app. The current app's design feels outdated and we like to add lots of new functionality and a new navigation as well. A complete overhaul therefore!
We want you to design 5 screens that will have changed the most. The complete wireframes of these 5 pages are attached in the requirements document.
Once the winning design is selected we will award the winner with the designing all other screens (40-50 screens based on the same design). This will be a separate project worth $1000. The winning designer can get more follow up work if both sides are happy about the cooperation.
We will give feedback as soon as the first screen has been uploaded for review. Final decision will be made only after all 5 screens are finished.
We hope you give it your best!
Note: will only communicate through PixelHarbor (no skype),
Updates
Reason: Want to give designers a chance to submit their designs as I understand from some, the deadline is too close.
I have raised the award and introduced a 2nd price as well to make it worth your time. I hope you give it your best shot.
Reason: A few of you have asked for an extension of the deadline as time is running out. I will extend by one day. Tell me if you need more.
Industry/Entity Type
Startup
Requirements
Must have
- At least 1 screen before we can give you feedback.
Nice to have
- multiple options of 1 screen to get to a desirable design

```html
<!DOCTYPE html>
<html lang="en">
<head>
<meta charset="utf-8">
<title>Home – Study Dashboard</title>
<link rel="stylesheet" href="https://fonts.googleapis.com/css2?family=Arimo:wght@400;700&display=swap">
<style>
  :root {
    --navy: #0f3050;
    --navy-deep: #0c2a47;
    --accent-blue: #1e88e5;
    --tab-active: #12b6ec;
    --page-bg: #efefef;
    --card-bg: #ffffff;
    --ink: #000000;
    --muted: #c2c2c2;
    --up-green: #2e7d1e;
    --down-red: #f07a7a;
    --line: #d9d9d9;
    --white: #ffffff;
  }
  * { box-sizing: border-box; margin: 0; padding: 0; }
  html, body { width: 800px; height: 1200px; overflow: hidden; }
  body {
    position: relative;
    background: var(--page-bg);
    font-family: "Arimo", Helvetica, Arial, sans-serif;
    color: var(--ink);
  }
  .status-bar {
    position: absolute; left: 0; top: 0; width: 800px; height: 50px;
    background: var(--navy); color: var(--white);
    font-size: 26px; display: flex; align-items: center;
  }
  .status-bar .carrier { position: absolute; left: 8px; display: flex; align-items: center; gap: 8px; }
  .status-bar .dots { display: flex; gap: 3px; }
  .status-bar .dot { width: 11px; height: 11px; border-radius: 50%; border: 1.5px solid var(--white); }
  .status-bar .dot.on { background: var(--white); }
  .status-bar .clock { position: absolute; left: 0; right: 0; text-align: center; }
  .status-bar .battery { position: absolute; right: 10px; display: flex; align-items: center; gap: 8px; }
  .battery-cell { width: 52px; height: 22px; border: 2px solid var(--white); border-radius: 4px; padding: 2px; position: relative; }
  .battery-cell::before { content: ""; display: block; width: 100%; height: 100%; background: var(--white); border-radius: 1px; }
  .battery-cell::after { content: ""; position: absolute; right: -6px; top: 5px; width: 3px; height: 8px; background: var(--white); border-radius: 0 2px 2px 0; }

  .app-header {
    position: absolute; left: 0; top: 50px; width: 800px; height: 110px;
    background: var(--navy);
  }
  .menu-button { position: absolute; left: 30px; top: 37px; width: 52px; height: 36px; }
  .menu-button span { position: absolute; left: 0; width: 52px; height: 6px; background: var(--white); border-radius: 2px; }
  .app-header h1 {
    position: absolute; left: 0; right: 0; top: 30px; text-align: center;
    color: var(--white); font-size: 40px; font-weight: 700;
  }

  .score-box {
    position: absolute; left: 30px; top: 176px; width: 171px; height: 164px;
    background: var(--card-bg); border: 2px solid var(--line); border-radius: 8px; text-align: center;
  }
  .score-box .value { font-size: 76px; line-height: 1; margin-top: 10px; letter-spacing: -1px; }
  .score-box .label { font-size: 30px; color: var(--muted); margin-top: 4px; }
  .score-box .delta { font-size: 27px; color: var(--down-red); margin-top: 2px; }

  .stat { position: absolute; top: 192px; text-align: center; width: 200px; margin-left: -100px; }
  .stat .figure { font-size: 30px; white-space: nowrap; }
  .stat .figure .change { color: var(--up-green); font-size: 27px; }
  .stat .caption { font-size: 27px; color: var(--muted); margin-top: 14px; }

  .period-switch {
    position: absolute; left: 229px; top: 296px; width: 537px; height: 40px;
    background: var(--navy-deep); color: var(--white); font-size: 28px;
    display: flex; align-items: center; justify-content: center;
  }
  .period-switch .step { position: absolute; top: 0; width: 45px; height: 40px; background: var(--accent-blue); display: flex; align-items: center; justify-content: center; }
  .period-switch .step.prev { left: 0; }
  .period-switch .step.next { right: 0; }

  .divider { position: absolute; left: 30px; top: 368px; width: 740px; height: 1px; background: var(--line); }

  .nav-card {
    position: absolute; left: 20px; width: 760px; height: 109px;
    background: var(--card-bg); border-top: 8px solid var(--ink); border-radius: 8px;
    display: flex; align-items: center; padding-left: 18px;
  }
  .nav-card .title { font-size: 43px; }
  .nav-card .icon { width: 48px; height: 40px; margin-right: 30px; }
  .nav-card .count { font-size: 48px; font-weight: 700; margin-right: 22px; }
  .chevron { position: absolute; right: 22px; top: 50%; transform: translateY(-50%); width: 22px; height: 34px; }

  .section-label { position: absolute; left: 20px; top: 853px; font-size: 26px; color: var(--muted); font-weight: 700; }

  .lesson-card {
    position: absolute; left: 20px; top: 902px; width: 760px; height: 108px;
    background: var(--card-bg); border-top: 8px solid var(--line); border-radius: 8px; padding: 14px 22px;
  }
  .lesson-card .lesson-number { font-size: 27px; font-weight: 700; }
  .lesson-card .lesson-name { font-size: 34px; margin-top: 6px; padding-left: 10px; }

  .tab-bar { position: absolute; left: 0; top: 1078px; width: 800px; height: 122px; background: var(--navy); }
  .tab {
    position: absolute; top: 0; width: 150px; height: 122px; margin-left: -75px;
    color: var(--white); text-align: center; font-size: 26px; font-weight: 700;
  }
  .tab svg { position: absolute; left: 50%; transform: translateX(-50%); top: 16px; }
  .tab .tab-label { position: absolute; left: 0; right: 0; bottom: 4px; }
  .tab.active { background: var(--tab-active); top: -9px; height: 131px; }
  .tab.active svg { top: 25px; }
</style>
</head>
<body>
  <div class="status-bar">
    <div class="carrier">
      <div class="dots"><span class="dot on"></span><span class="dot on"></span><span class="dot on"></span><span class="dot"></span><span class="dot"></span></div>
      <span>Nuvia</span>
      <svg width="28" height="22" viewBox="0 0 28 22"><path d="M2 8a17 17 0 0 1 24 0M6 12a11 11 0 0 1 16 0M10 16a5 5 0 0 1 8 0" fill="none" stroke="#fff" stroke-width="3" stroke-linecap="round"/><circle cx="14" cy="19" r="2" fill="#fff"/></svg>
    </div>
    <div class="clock">23:12</div>
    <div class="battery">
      <svg width="16" height="26" viewBox="0 0 16 26"><path d="M2 7l12 12-6 5V2l6 5L2 19" fill="none" stroke="#fff" stroke-width="2"/></svg>
      <span>100%</span>
      <span class="battery-cell"></span>
    </div>
  </div>

  <header class="app-header">
    <div class="menu-button"><span style="top:0"></span><span style="top:15px"></span><span style="top:30px"></span></div>
    <h1>Welcome back, Noam</h1>
  </header>

  <section class="score-box">
    <div class="value">650</div>
    <div class="label">SCORE</div>
    <div class="delta">&#8595; -18</div>
  </section>

  <div class="stat" style="left:319px"><div class="figure">34%<span class="change">&#8593;+10</span></div><div class="caption">completion</div></div>
  <div class="stat" style="left:519px"><div class="figure">20<span class="change">&#8593;+3</span></div><div class="caption">sessions</div></div>
  <div class="stat" style="left:694px"><div class="figure">18<span class="change">&#8593;+10</span></div><div class="caption">min.</div></div>

  <div class="period-switch">
    <span class="step prev"><svg width="14" height="22" viewBox="0 0 14 22"><path d="M11 3L4 11l7 8" fill="none" stroke="#fff" stroke-width="3"/></svg></span>
    this week
    <span class="step next"><svg width="14" height="22" viewBox="0 0 14 22"><path d="M3 3l7 8-7 8" fill="none" stroke="#fff" stroke-width="3"/></svg></span>
  </div>

  <div class="divider"></div>

  <a class="nav-card" style="top:406px">
    <svg class="icon" viewBox="0 0 48 40"><rect x="1" y="1" width="46" height="38" fill="none" stroke="#000" stroke-width="2"/><path d="M6 32l10-12 8 7 16-17" fill="none" stroke="#000" stroke-width="2"/><path d="M34 10h6v6" fill="none" stroke="#000" stroke-width="2"/></svg>
    <span class="title">Analytics</span>
    <svg class="chevron" viewBox="0 0 22 34"><path d="M4 4l13 13L4 30" fill="none" stroke="#000" stroke-width="4"/></svg>
  </a>

  <a class="nav-card" style="top:558px">
    <svg class="icon" viewBox="0 0 48 40"><g fill="none" stroke="#000" stroke-width="2"><circle cx="5" cy="6" r="3"/><circle cx="5" cy="20" r="3"/><circle cx="5" cy="34" r="3"/><path d="M14 6h32M14 20h32M14 34h32"/></g></svg>
    <span class="title">Course Overview</span>
    <svg class="chevron" viewBox="0 0 22 34"><path d="M4 4l13 13L4 30" fill="none" stroke="#000" stroke-width="4"/></svg>
  </a>

  <a class="nav-card" style="top:704px">
    <span class="count">33</span>
    <span class="title">Days until test</span>
    <svg class="chevron" viewBox="0 0 22 34"><path d="M4 4l13 13L4 30" fill="none" stroke="#000" stroke-width="4"/></svg>
  </a>

  <div class="section-label">Up Next:</div>

  <a class="lesson-card">
    <div class="lesson-number">Lesson 3</div>
    <div class="lesson-name">Essay Writing</div>
    <svg class="chevron" viewBox="0 0 22 34"><path d="M4 4l13 13L4 30" fill="none" stroke="#000" stroke-width="4"/></svg>
  </a>

  <nav class="tab-bar">
    <div class="tab" style="left:75px">
      <svg width="58" height="64" viewBox="0 0 58 64"><g fill="none" stroke="#fff" stroke-width="3"><rect x="4" y="2" width="48" height="58"/><path d="M10 2v58M52 8h4v54H10"/></g></svg>
      <span class="tab-label">Theory</span>
    </div>
    <div class="tab" style="left:237px">
      <svg width="60" height="64" viewBox="0 0 60 64"><g fill="none" stroke="#fff" stroke-width="3"><path d="M44 4l12 12L20 52 6 58l6-14z"/><path d="M38 10l12 12M12 44l8 8"/></g></svg>
      <span class="tab-label">Practice</span>
    </div>
    <div class="tab active" style="left:400px">
      <svg width="66" height="62" viewBox="0 0 66 62"><path d="M33 3L2 30h9v30h17V42h10v18h17V30h9L52 19V6h-8v6z" fill="#fff"/></svg>
      <span class="tab-label">Home</span>
    </div>
    <div class="tab" style="left:562px">
      <svg width="62" height="64" viewBox="0 0 62 64"><g fill="none" stroke="#fff" stroke-width="3"><circle cx="31" cy="10" r="7"/><path d="M31 17v24"/><rect x="4" y="41" width="54" height="16" rx="3"/><path d="M20 41v-4h22v4M10 57v4h42v-4"/></g></svg>
      <span class="tab-label">Games</span>
    </div>
    <div class="tab" style="left:725px">
      <svg width="50" height="64" viewBox="0 0 50 64"><g fill="none" stroke="#fff" stroke-width="3"><path d="M3 3h30l14 14v44H3z"/><path d="M33 3v14h14M11 24h28M11 32h28M11 40h28M11 48h28"/></g></svg>
      <span class="tab-label">Test</span>
    </div>
  </nav>
</body>
</html>
```